Terravista NQ PPT template - non-profit company - minerals, energy, water, geothermal resources

Terravista NQ requires two (Letter-sized and 16:9)simple, flexible and clean PowerPoint templates that can be used for corporate and research project presentations and meeting materials

Each layout should have correct colours, fonts and size as a default (focus area colours for headings; secondary colours for body text). Each slide should have the Terravista NQ logo. Slide number should be automatically generated, with no slide number on title slide.

Target Market(s)

Varied, but almost always professional: Government; Community leaders; Mineral/Energy industries; and Academic researchers.

Font styles to use
Serif
Sans Serif
Other font styles liked:
• Calibri, or whatever in style guide

Requirements
Must have
• Two version that we can use – both need to match:
- 16:9 slide size for on-screen presentations; and
- Letter (8.5 x 11 inch) for meeting materials that are printed.

Must use colours in logo as listed in the style guide
Nice to have
• Consistency
Should not have
• Should not be black and white - needs colour

```html
<!DOCTYPE html>
<html lang="en">
<head>
<meta charset="utf-8">
<title>Terravista NQ Template Pages</title>
<link rel="stylesheet" href="https://fonts.googleapis.com/css2?family=Cabin:wght@400;500;600;700&family=Open+Sans:wght@400;600;700&display=swap">
<style>
:root{
  --orange:#e0793a;
  --green:#3aa548;
  --blue:#2aa0cf;
  --slate:#55606b;
  --ink:#2b2f33;
  --body:#6b6f74;
  --paper:#ffffff;
  --canvas:#ffffff;
  --red:#d9322c;
}
*{box-sizing:border-box;margin:0;padding:0}
html,body{width:771px;height:1200px;overflow:hidden;background:var(--canvas)}
body{position:relative;font-family:"Open Sans",Arial,sans-serif;color:var(--body)}
.page{position:absolute;width:193px;height:279px;background:var(--paper);overflow:hidden;box-shadow:0 1px 4px rgba(0,0,0,.28)}
.page::before{content:"";position:absolute;left:0;top:0;right:0;height:2px;z-index:5;
  background:linear-gradient(90deg,var(--orange) 0 34%,var(--green) 34% 67%,var(--blue) 67% 100%)}
.abs{position:absolute}
.ph{position:absolute}
.ph-map{background:linear-gradient(135deg,#5f7d4f,#8a8db0 30%,#6f9160 55%,#a08fb8 75%,#6b7f55)}
.ph-rock{background:linear-gradient(150deg,#8a6a52,#c28a5e 35%,#d8cfc4 60%,#7d6b5e)}
.ph-cliff{background:linear-gradient(160deg,#6f95c0,#b07a45 40%,#5d4733 75%,#bfa788)}
.ph-people{background:linear-gradient(170deg,#d9dde2,#8d97a3 45%,#5e5a50 80%)}
.ph-office{background:linear-gradient(160deg,#c9b9a4,#7d8fa8 50%,#d04d3b 70%,#f0d35a)}
.ph-sky{background:linear-gradient(180deg,#a9adb2,#d6d6d2 40%,#6d6e6a 70%,#2f302c)}
.ph-dusk{background:linear-gradient(180deg,#e2a855,#a47a4a 40%,#2d2a25)}
.ph-field{background:linear-gradient(180deg,#7a8f6a,#c7a27b 45%,#4f8fb8)}
.ph-grid{background:linear-gradient(135deg,#dfe6d8,#a8c29a 50%,#e9eef2)}
.ph-blank{background:linear-gradient(180deg,#9c9c9c,#e8e8e8)}
.brand{position:absolute;left:17px;bottom:6px;font-family:"Cabin",sans-serif;font-weight:700;font-size:6px;color:var(--slate);display:flex;align-items:center;gap:3px}
.brand .dot{width:4px;height:4px;border-radius:50%;background:var(--orange)}
.folio{position:absolute;right:14px;bottom:8px;font-size:3.6px;color:var(--ink)}
.tiny{font-size:3.3px;line-height:1.45;text-align:justify}
.head{font-family:"Cabin",sans-serif;font-weight:500;line-height:.98}
.o{color:var(--orange)} .g{color:var(--green)} .s{color:var(--slate)} .k{color:var(--ink)}
ul.contents{list-style:none;font-family:"Cabin",sans-serif;font-size:5.6px;line-height:1.3}
ul.contents li{position:relative;padding-left:8px;margin-bottom:2.5px}
ul.contents li::before{content:"•";position:absolute;left:0}
.refs{font-size:2.6px;color:var(--red);text-decoration:underline;line-height:1.4}
</style>
</head>
<body>

<!-- Row 1 -->
<section class="page cover" style="left:46px;top:16px">
  <div class="ph ph-map" style="left:0;top:0;width:193px;height:279px" role="img" aria-label="Aerial mineral map imagery in green and violet tones"></div>
  <div class="abs" style="left:0;top:0;width:193px;height:56px;background:rgba(222,222,226,.88)"></div>
  <div class="abs s" style="left:0;top:30px;width:193px;text-align:center;font-family:Cabin,sans-serif;font-weight:700;font-size:12px">Terravista NQ</div>
  <div class="abs" style="left:0;top:205px;width:193px;height:50px;background:rgba(215,215,218,.85)"></div>
  <div class="abs s head" style="left:0;top:214px;width:193px;text-align:center;font-size:20px;font-weight:600;letter-spacing:-.4px">Monthly Report</div>
  <div class="abs s" style="left:0;top:238px;width:193px;text-align:center;font-family:Cabin,sans-serif;font-size:7px;font-weight:600">May 2020</div>
</section>

<section class="page message" style="left:295px;top:16px">
  <div class="ph ph-people" style="left:0;top:2px;width:96px;height:138px" role="img" aria-label="Two researchers reviewing a colour geological map"></div>
  <div class="abs s head" style="left:104px;top:53px;font-size:17px;font-weight:600">CHAIR &amp;<br>CEO<br>MESSAGE</div>
  <div class="ph ph-cliff" style="left:96px;top:140px;width:97px;height:139px" role="img" aria-label="Helicopter landed on a mountain ridge"></div>
  <div class="abs tiny k" style="left:12px;top:176px;width:75px;font-weight:600">Our collaborative approach is generating more coordinated, relevant research projects and broadening the awareness of the fundamental value of public geoscience to everyone.</div>
  <div class="abs tiny k" style="left:12px;top:203px;width:75px;font-weight:600">Sharing results publicly and developing understanding of Terravista NQ's research is stimulating innovation, informing investment and resource development decisions and catalyzing socio-economic opportunities in many regions of the province.</div>
  <div class="brand"><span class="dot"></span>Terravista NQ</div>
</section>

<section class="page section-minerals" style="left:534px;top:16px">
  <div class="ph ph-rock" style="left:121px;top:0;width:72px;height:279px" role="img" aria-label="Close view of layered orange and grey rock"></div>
  <div class="abs" style="left:0;top:0;width:121px;height:279px;background:linear-gradient(90deg,#fff 80%,rgba(255,255,255,.6))"></div>
  <div class="abs o head" style="left:10px;top:7px;font-size:25px;font-weight:700;line-height:.95">MI<br>NE<br>RA<br>LS</div>
  <div class="abs o" style="left:8px;top:116px;width:109px;font-family:Cabin,sans-serif;font-size:4.4px;font-weight:600;word-spacing:8px">Identifying New Natural Resource Opportunities</div>
  <div class="abs o tiny" style="left:8px;top:128px;width:109px;font-weight:700">We are helping to identify new natural resource opportunities in the province by investing in minerals projects that deliver new earth science research and baseline data for prospectors, explorers, mine developers, governments, community leaders and Indigenous groups.</div>
  <div class="abs o" style="left:8px;top:178px;font-family:Cabin,sans-serif;font-size:6px;font-weight:600">Content</div>
  <ul class="abs contents o" style="left:8px;top:189px;width:112px;font-weight:600">
    <li>Identifying New Natural Resource Opportunities</li>
    <li>Major New Regional Projects Announced</li>
    <li>Preserving Regional Earth Science Legacy</li>
    <li>Tools for Mineral Discovery</li>
  </ul>
  <svg class="abs" style="left:146px;top:116px" width="48" height="48" viewBox="0 0 48 48" aria-hidden="true">
    <circle cx="24" cy="24" r="24" fill="#fff"/>
    <path d="M13 20 Q24 9 36 16" fill="none" stroke="#e0793a" stroke-width="2"/>
    <path d="M26 14 L16 36" stroke="#e0793a" stroke-width="2.2" stroke-linecap="round"/>
  </svg>
</section>

<!-- Row 2 -->
<section class="page projects" style="left:46px;top:311px">
  <div class="ph ph-map" style="left:0;top:0;width:193px;height:124px" role="img" aria-label="Aerial mineral map imagery"></div>
  <div class="abs o head" style="left:16px;top:137px;font-size:15px;font-weight:600">Major New Regional<br>Projects Announced</div>
  <div class="abs o" style="left:16px;top:175px;width:165px;font-size:5.8px;line-height:2">In 2019, we launched two new major minerals projects that are delivering new earth science information to focus the search for mineral deposits, increase discovery rates, encourage investment and promote responsible mineral development in our province.</div>
  <div class="brand"><span class="dot"></span>Terravista NQ</div>
  <div class="folio">4</div>
</section>

<section class="page tools" style="left:295px;top:311px">
  <div class="abs o head" style="left:19px;top:26px;font-size:14px;font-weight:600;letter-spacing:.5px;line-height:1.45">Tools for Mineral<br>Discovery</div>
  <div class="abs o tiny" style="left:19px;top:67px;width:156px;text-align:left">To help find new mineral deposits across the province, we are advancing innovative new mineral exploration tools and methods.</div>
  <div class="abs o tiny" style="left:19px;top:79px;width:156px">Lorem Ipsum is simply dummy text of the printing and typesetting industry. Lorem Ipsum has been the industry's standard dummy text ever since the 1500s, when an unknown printer took a galley of type and scrambled it to make a type specimen book. It has survived not only five centuries, but also the leap into electronic typesetting, remaining essentially unchanged. It was popularized in the 1960s with the release of transfer sheets containing Lorem Ipsum passages.</div>
  <div class="ph ph-rock" style="left:0;top:140px;width:65px;height:111px" role="img" aria-label="Geologist climbing a rock slope"></div>
  <div class="ph ph-map" style="left:65px;top:140px;width:64px;height:111px" role="img" aria-label="Satellite mineral imagery"></div>
  <div class="ph ph-rock" style="left:129px;top:140px;width:64px;height:111px;filter:hue-rotate(-20deg) brightness(1.1)" role="img" aria-label="Layered rock texture"></div>
  <div class="brand"><span class="dot"></span>Terravista NQ</div>
  <div class="folio">5</div>
</section>

<section class="page minerals-research" style="left:534px;top:311px">
  <div class="abs o head" style="left:8px;top:13px;font-size:12px;font-weight:600">MINERALS</div>
  <div class="abs o head" style="left:8px;top:28px;font-size:8px;line-height:1.25">Research to Support<br>Future Global<br>Minerals Demand</div>
  <div class="abs o tiny" style="left:8px;top:62px;width:82px">Regional deposits include copper, gold, molybdenum, silver and zinc, as well as steel-making coal and industrial minerals.</div>
  <div class="abs o tiny" style="left:8px;top:80px;width:82px">Global demand for many of these commodities is set to grow in coming years.</div>
  <div class="abs o tiny" style="left:8px;top:93px;width:82px">Exploration and mining play a vital role in the regional economy.</div>
  <div class="abs o tiny" style="left:8px;top:106px;width:82px">New and innovative public research is needed to solve challenges and attract investment.</div>
  <div class="abs k" style="left:8px;top:171px;width:82px;font-size:4px;font-weight:700">Identifying New Natural Resource Opportunities</div>
  <div class="abs k tiny" style="left:8px;top:184px;width:82px">Our goals are to continue regional-scale surveys, deliver large data sets, identify prospective targets and add value to existing data through ground-truthing and mining camp compilations.</div>
  <div class="abs" style="left:20px;top:235px;width:45px;border-top:.4px solid #999"></div>
  <div class="abs refs" style="left:10px;top:238px;width:80px">1. reference link<br>2. reference link<br>3. reference link</div>
  <div class="abs k" style="left:102px;top:10px;width:84px;font-size:4px;font-weight:700;line-height:1.5">Minerals in the Kootenay Boundary Region</div>
  <div class="abs tiny" style="left:102px;top:29px;width:84px">Lorem Ipsum is simply dummy text of the printing and typesetting industry. Lorem Ipsum has been the industry's standard dummy text ever since the 1500s, when an unknown printer took a galley of type and scrambled it to make a type specimen book. It has survived not only five centuries, but also the leap into electronic typesetting, remaining essentially unchanged.</div>
  <div class="abs tiny" style="left:102px;top:115px;width:84px">Lorem Ipsum is simply dummy text of the printing and typesetting industry. Lorem Ipsum has been the industry's standard dummy text ever since the 1500s.</div>
  <div class="ph ph-people" style="left:96px;top:140px;width:97px;height:117px" role="img" aria-label="Two field geologists on a mountain outcrop"></div>
  <div class="abs" style="left:140px;top:258px;font-size:2.6px;font-style:italic">Photo credit</div>
  <div class="brand"><span class="dot"></span>Terravista NQ</div>
  <div class="folio">6</div>
</section>

<!-- Row 3 -->
<section class="page section-energy" style="left:47px;top:607px">
  <div class="ph ph-sky" style="left:121px;top:0;width:72px;height:279px" role="img" aria-label="Steam rising from a geothermal field under cloudy sky"></div>
  <div class="abs" style="left:0;top:0;width:121px;height:279px;background:#f7f8f8"></div>
  <div class="abs g head" style="left:10px;top:6px;font-size:24px;font-weight:600;line-height:1.05">OIL<br>&amp;<br>GAS</div>
  <div class="abs g tiny" style="left:8px;top:119px;width:110px;font-size:4.3px">We are collecting, interpreting and sharing new scientific data relating to natural gas development to guide clean, responsible energy development, minimize impacts, answer specific environmental and social questions and attract investment to the province.</div>
  <div class="abs g" style="left:8px;top:180px;font-family:Cabin,sans-serif;font-size:6px;font-weight:600">Content</div>
  <ul class="abs contents g" style="left:8px;top:191px;width:112px">
    <li>Facilitating Responsible Natural Resource Development</li>
    <li>Innovation &amp; Technology</li>
    <li>Geothermal</li>
  </ul>
  <svg class="abs" style="left:133px;top:120px" width="48" height="48" viewBox="0 0 48 48" aria-hidden="true">
    <circle cx="24" cy="24" r="23.5" fill="#fff" stroke="#3aa548" stroke-width=".6"/>
    <path d="M18 26 Q14 21 17 16 Q21 11 27 12 Q33 14 33 20 Q33 24 30 27 L29 30 H19 Z" fill="none" stroke="#3aa548" stroke-width="1.2"/>
    <path d="M19 32 H29 M20 34.5 H28 M22 37 H26" stroke="#3aa548" stroke-width="1.2"/>
    <path d="M24 5 V9 M11 10 L14 13 M37 10 L34 13 M7 21 H10 M38 21 H41" stroke="#3aa548" stroke-width="1"/>
  </svg>
</section>

<section class="page expose" style="left:295px;top:607px">
  <div class="abs g head" style="left:17px;top:44px;font-size:15px;font-weight:600">More<br>Space For<br>Expose<br>Work &amp;<br>Develop</div>
  <div class="abs g" style="left:19px;top:132px;font-size:4.4px;font-weight:700">Oil &amp; Gas Subtitle</div>
  <div class="abs tiny" style="left:19px;top:144px;width:92px;line-height:1.9">Lorem Ipsum is simply dummy text of the printing and typesetting industry. Lorem Ipsum has been the industry's standard dummy text ever since the 1500s, when an unknown printer took a galley of type and scrambled it to make a type specimen book. It has survived not only five centuries, but also the leap into electronic typesetting, remaining essentially unchanged. It was popularized in the 1960s with the release of transfer sheets containing Lorem Ipsum passages.</div>
  <div class="abs tiny" style="left:19px;top:225px;width:92px;line-height:1.9">Lorem Ipsum is simply dummy text of the printing and typesetting industry. Lorem Ipsum has been the industry's standard dummy text ever since the 1500s.</div>
  <div class="ph ph-dusk" style="left:124px;top:2px;width:69px;height:139px" role="img" aria-label="Survey drone on the ground at sunset"></div>
  <div class="ph ph-field" style="left:124px;top:141px;width:69px;height:138px" role="img" aria-label="Field scientist holding a water sample"></div>
  <div class="brand"><span class="dot"></span>Terravista NQ</div>
</section>

<section class="page energy-research" style="left:534px;top:607px">
  <div class="ph ph-grid" style="left:3px;top:6px;width:49px;height:57px;border:.5px solid #8aa" role="img" aria-label="Regional map of wells and survey areas"></div>
  <div class="abs g head" style="left:59px;top:7px;font-size:16px;font-weight:600">OIL &amp; GAS</div>
  <div class="abs g" style="left:60px;top:24px;width:122px;font-size:4.2px;font-weight:700;word-spacing:3px">Innovative Energy Research as a Competitive Advantage</div>
  <div class="abs g tiny" style="left:60px;top:36px;width:122px">The energy sector supports thousands of jobs and supplies domestic and global markets. Investment in oil and gas reached new highs, and production is forecast to increase in coming years. Collecting and sharing new scientific data helps guide clean, responsible energy development.</div>
  <div class="abs g" style="left:0;top:99px;width:193px;text-align:center;font-size:5.5px">Facilitating Responsible Natural Resource Development</div>
  <div class="abs tiny" style="left:6px;top:111px;width:83px">We have been funding research investigating induced seismicity caused by human activity and natural gas development in the northeast region, especially in areas close to communities and infrastructure.</div>
  <div class="abs tiny" style="left:6px;top:142px;width:83px">Numerous factors influence the potential for hydraulic fracturing and wastewater disposal to cause earthquakes, including stress, fault orientation and injection rate.</div>
  <div class="abs" style="left:6px;top:226px;font-size:4px">Northeast Focus</div>
  <div class="abs tiny" style="left:6px;top:233px;width:83px">This research focuses on a gas-prone play within a major sedimentary basin.</div>
  <div class="abs tiny" style="left:97px;top:111px;width:86px;text-align:left">Our induced seismicity research is guided by subject matter experts and by reports such as:</div>
  <ul class="abs tiny" style="left:103px;top:122px;width:80px;text-align:left;padding-left:3px">
    <li>Investigation of observed seismicity in the basin</li>
    <li>Investigation of observed seismicity in the trend</li>
    <li>Environmental impacts of shale gas extraction</li>
    <li>Scientific review of hydraulic fracturing in the region</li>
  </ul>
  <div class="ph ph-office" style="left:99px;top:169px;width:78px;height:71px" role="img" aria-label="Audience attending a research presentation"></div>
  <div class="abs refs" style="left:102px;top:248px;width:80px">1. reference link<br>2. reference link<br>3. reference link</div>
  <div class="brand"><span class="dot"></span>Terravista NQ</div>
  <div class="folio">8</div>
</section>

<!-- Row 4 -->
<section class="page more-minerals" style="left:55px;top:903px">
  <div class="abs o head" style="left:17px;top:14px;font-size:15px;font-weight:600;letter-spacing:.3px">More for Minerals</div>
  <div class="abs o" style="left:18px;top:48px;font-size:4.2px;font-weight:700">Lorem Ipsum is simply dummy</div>
  <div class="abs tiny" style="left:18px;top:54px;width:76px">Lorem Ipsum is simply dummy text of the printing and typesetting industry. Lorem Ipsum has been the industry's standard dummy text ever since the 1500s, when an unknown printer took a galley of type and scrambled it to make a type specimen book. It has survived not only five centuries, remaining essentially unchanged.</div>
  <div class="ph ph-rock" style="left:97px;top:47px;width:80px;height:72px" role="img" aria-label="Geologist on a rock slope"></div>
  <div class="ph ph-cliff" style="left:17px;top:120px;width:80px;height:72px" role="img" aria-label="Helicopter on a mountain ridge"></div>
  <div class="abs o" style="left:100px;top:121px;font-size:4.2px;font-weight:700">Lorem Ipsum is simply dummy</div>
  <div class="abs tiny" style="left:100px;top:127px;width:76px">Lorem Ipsum is simply dummy text of the printing and typesetting industry. Lorem Ipsum has been the industry's standard dummy text ever since the 1500s, when an unknown printer took a galley of type and scrambled it to make a type specimen book. It has survived not only five centuries, remaining essentially unchanged.</div>
  <div class="abs o" style="left:18px;top:194px;font-size:4.2px;font-weight:700">Lorem Ipsum is simply dummy</div>
  <div class="abs tiny" style="left:18px;top:200px;width:76px">Lorem Ipsum is simply dummy text of the printing and typesetting industry. Lorem Ipsum has been the industry's standard dummy text ever since the 1500s, when an unknown printer took a galley of type and scrambled it to make a type specimen book. It has survived not only five centuries, remaining essentially unchanged.</div>
  <div class="ph ph-people" style="left:97px;top:193px;width:80px;height:71px" role="img" aria-label="Two field geologists on an outcrop"></div>
  <div class="brand"><span class="dot"></span>Terravista NQ</div>
  <div class="folio">10</div>
</section>

<section class="page two-image" style="left:295px;top:903px">
  <div class="ph ph-blank" style="left:96px;top:2px;width:97px;height:140px" role="img" aria-label="Image placeholder"></div>
  <div class="ph ph-blank" style="left:48px;top:142px;width:48px;height:82px" role="img" aria-label="Image placeholder"></div>
  <div class="abs head" style="left:17px;top:48px;font-size:12px;font-weight:600"><span class="k">Two<br>Image</span><br><span class="o">Layout</span></div>
  <div class="abs k" style="left:110px;top:168px;font-size:4.2px;font-weight:700">Subtitle</div>
  <div class="abs k" style="left:110px;top:180px;width:68px;font-size:3.6px;line-height:1.8">A peep at some distant orb has power to raise and purify our thoughts like a strain of sacred music, or a noble picture, or a passage from the grander poets. It always does one good.</div>
  <div class="brand"><span class="dot"></span>Terravista NQ</div>
  <div class="folio">41</div>
</section>

<section class="page four-image" style="left:534px;top:903px">
  <div class="ph ph-blank" style="left:96px;top:2px;width:97px;height:139px" role="img" aria-label="Image placeholder"></div>
  <div class="ph ph-blank" style="left:96px;top:141px;width:97px;height:138px;background:linear-gradient(180deg,#a3a3a3,#ececec)" role="img" aria-label="Image placeholder"></div>
  <div class="abs head" style="left:17px;top:48px;font-size:12px;font-weight:600"><span class="k">Four<br>Image</span><br><span class="o">Layout</span></div>
  <div class="abs k" style="left:32px;top:151px;font-size:4.2px;font-weight:700">Subtitle</div>
  <div class="abs k" style="left:32px;top:163px;width:58px;font-size:3.6px;line-height:1.8">A peep at some distant orb has power to raise and purify our thoughts like a strain of sacred music, or a noble picture, or a passage from the grander poets. It always does one good.</div>
  <div class="abs k" style="left:32px;top:207px;width:58px;font-size:3.6px;line-height:1.8">A peep at some distant orb has power to raise and purify our thoughts like a strain of sacred music.</div>
  <div class="brand"><span class="dot"></span>Terravista NQ</div>
  <div class="folio">40</div>
</section>

</body>
</html>
```